Corvane Lending Partners. Professional and Established Company

A full service finance company specializing in obtaining capital for small business. Business Lending advisor, helping small business owners access the capital they need to launch, grow, or sustain their business. Many of our programs offer flexible guidelines to overcome common obstacles such as credit score, credit history, and time in business, financials, and industry type. Our streamlined funding process makes getting a business loan, business line of credit, stated income commercial real estate loan, a smooth and stress free experience.SOME OF THE MOST COMMON NEEDS FOR BUSINESS CAPITAL:• Working Capital• Debt Consolidations (loans, merchant cash advances, etc.)• Payroll• Operating Expenses• Inventory• Equipment Financing• Commercial Real Estate (Purchase, Fix & Flip, Rehab, Renovations)• Business Acquisitions• Business ExpansionWe like the websites:www.quillmorecf.com they are in the same industry and provide the same servicesWe are wanting to be able to update when we do press releases and such using Word Press. Our look should be very professional and we will be adding Our Team Professional Bios and Headshots.

Industry/Entity Type

Finance

Number of Pages Required

5+ page

Font styles to use
Serif
Sans Serif

Requirements
Must have
• We want to copy quillmorecf.com
• We need:
• Home Page
• About Us
• Loan Programs
• Loan Criteria
• News
• Apply Now
• Contact
Nice to have
• See quillmorecf.com
Should not have
• Need professional design. Nothing bright or abstract

```html
<!DOCTYPE html>
<html lang="en">
<head>
<meta charset="utf-8">
<title>Corvane Lending Partners</title>
<link href="https://fonts.googleapis.com/css2?family=Cinzel:wght@400;700&family=Open+Sans:wght@400;600;700&display=swap" rel="stylesheet">
<style>
:root{
  --blue:#2b6cb0;
  --blue-dark:#1f4f86;
  --ink:#333a40;
  --muted:#6b737b;
  --nav:#4a4f55;
  --nav-active:#7c8288;
  --light:#eceff2;
  --white:#ffffff;
  --contact:#26292c;
  --footer:#1d5fa3;
}
*{box-sizing:border-box;margin:0;padding:0}
html,body{width:1200px;height:3988px;overflow:hidden}
body{font-family:"Open Sans",Arial,sans-serif;color:var(--ink);background:var(--white);font-size:14px;line-height:1.6}
.serif{font-family:"Cinzel",Georgia,serif}

/* header */
.site-header{height:100px;display:flex;align-items:center;padding:0 40px 0 60px;background:var(--white)}
.brand{display:flex;flex-direction:column;line-height:1}
.brand-name{font-family:"Cinzel",Georgia,serif;font-weight:700;font-size:30px;color:var(--blue-dark);letter-spacing:1px}
.brand-sub{font-family:"Cinzel",Georgia,serif;font-weight:700;font-size:11px;color:var(--blue-dark);letter-spacing:3px;margin-top:4px}
.header-contacts{margin-left:auto;display:flex;gap:44px;align-items:center}
.hc-item{display:flex;align-items:center;gap:10px;font-size:12px;line-height:1.35}
.hc-item b{display:block;font-size:11px;color:var(--muted);font-weight:600}
.hc-icon{width:30px;height:30px;border-radius:50%;border:1px solid #c8cdd2;display:flex;align-items:center;justify-content:center}
.btn-quote{margin-left:30px;background:var(--nav);color:var(--white);font-size:12px;font-weight:700;padding:9px 16px;letter-spacing:1px}

/* hero */
.hero{position:relative;height:580px}
.hero-photo{position:absolute;inset:0;background:linear-gradient(180deg,#1c3c66 0%,#4a7fb8 35%,#8fb5d8 60%,#3f6994 100%)}
.main-nav{position:relative;height:32px;background:var(--nav);display:flex;justify-content:center;gap:0}
.main-nav a{color:var(--white);text-decoration:none;font-size:12px;font-weight:600;padding:0 30px;line-height:32px;letter-spacing:.5px}
.main-nav a.active{background:var(--nav-active)}
.hero-copy{position:relative;text-align:center;margin-top:210px;color:var(--white)}
.hero-copy h1{font-family:"Cinzel",Georgia,serif;font-weight:700;font-size:30px;line-height:1.35;letter-spacing:1px}
.btn{display:inline-block;background:var(--blue);color:var(--white);font-size:12px;font-weight:700;letter-spacing:1px;padding:10px 22px;border:1px solid rgba(255,255,255,.5)}
.hero-copy .btn{margin-top:18px}

/* section titles */
.section-title{font-family:"Cinzel",Georgia,serif;font-weight:700;font-size:30px;text-align:center;color:var(--ink);letter-spacing:1px}
.section-title span{color:var(--blue)}
.title-rule{width:60px;height:2px;background:var(--blue);margin:12px auto 0}

/* about */
.about{height:330px;padding-top:58px;text-align:center}
.about .lead{color:var(--blue);font-weight:700;font-size:14px;margin:26px auto 8px;width:1040px}
.about p.body{width:1040px;margin:0 auto;font-size:13px;color:var(--muted)}
.about .btn{margin-top:26px;padding:8px 22px}

/* closed loans */
.closed{height:390px;background:var(--light);padding-top:56px;position:relative}
.loan-cards{display:flex;justify-content:center;margin-top:48px}
.loan-card{width:250px;height:160px;background:var(--white);text-align:center;padding-top:24px;box-shadow:0 2px 6px rgba(0,0,0,.08)}
.loan-card.featured{background:var(--blue);color:var(--white);height:180px;margin-top:-10px;padding-top:34px}
.loan-card .kind{font-size:12px;font-weight:700;letter-spacing:1px}
.loan-card .amount{font-size:26px;margin:10px 0 10px;font-weight:400}
.loan-card .note{font-size:12px;line-height:1.5}
.slider-arrow{position:absolute;top:230px;width:30px;height:30px;border-radius:50%;background:#c9ced3;display:flex;align-items:center;justify-content:center}

/* news */
.news{padding-top:30px}
.news-row{display:flex;position:relative}
.news-row.one{height:178px;margin-top:60px}
.news-row.two{height:288px}
.news-panel{background:linear-gradient(90deg,rgba(31,79,134,.95),rgba(43,108,176,.85));color:var(--white);padding:22px 36px}
.news-panel h3{font-family:"Cinzel",Georgia,serif;font-weight:400;font-size:19px;line-height:1.3}
.news-panel p{font-size:12px;margin-top:10px;opacity:.9}
.news-panel .more{font-size:12px;font-weight:700;margin-top:8px;display:block}
.photo{display:block}

/* programs */
.programs{height:702px;padding-top:64px}
.program-grid{display:grid;grid-template-columns:repeat(3,300px);column-gap:60px;row-gap:40px;justify-content:center;margin-top:56px}
.program{display:flex;gap:16px}
.program-icon{flex:0 0 56px;height:56px;border-radius:50%;background:var(--blue-dark);display:flex;align-items:center;justify-content:center}
.program h4{font-family:"Cinzel",Georgia,serif;font-size:14px;font-weight:700;margin-top:4px}
.program p{font-size:12px;color:var(--muted);line-height:1.45;margin-top:4px}

/* team */
.team{height:760px;padding-top:46px;position:relative}
.team-cards{display:flex;justify-content:center;gap:22px;margin-top:72px}
.team-card{width:255px;position:relative}
.team-photo{height:400px}
.team-tag{position:absolute;left:0;right:0;bottom:0;text-align:center;padding:14px 10px;background:rgba(255,255,255,.92);font-size:11px}
.team-card.featured .team-tag{background:var(--blue);color:var(--white);height:150px;padding-top:22px}
.team-tag .name{font-family:"Cinzel",Georgia,serif;font-weight:700;font-size:13px}
.team-tag .role{font-size:11px;margin-top:2px}
.team-tag .line{font-size:11px;margin-top:6px}
.team .slider-arrow{top:420px}

/* contact */
.contact{position:relative;height:340px;background:var(--contact);color:var(--white)}
.contact-bg{position:absolute;inset:0;background:linear-gradient(90deg,#2a2d30 0%,#33373b 45%,#4a4f54 75%,#2b2e31 100%)}
.contact-inner{position:relative;padding-top:26px}
.contact h2{font-family:"Cinzel",Georgia,serif;font-weight:700;font-size:26px;text-align:center}
.contact-body{display:flex;margin-top:50px;padding:0 150px}
.contact-info .brand-name{color:var(--white);font-size:34px}
.contact-info .brand-sub{color:var(--white)}
.contact-info ul{list-style:none;margin-top:20px;font-size:12px}
.contact-info li{display:flex;gap:10px;align-items:center;margin-bottom:6px}
.contact-form{margin-left:auto;width:250px;display:flex;flex-direction:column;gap:6px}
.field{height:26px;border:1px solid rgba(255,255,255,.5);background:rgba(0,0,0,.35);font-size:11px;padding:4px 8px;color:#d7dbe0}
.field.msg{height:56px}
.contact-form .btn{align-self:flex-start;padding:6px 18px;font-size:11px}

/* map */
.map{position:relative;height:200px}
.map-area{position:absolute;inset:0;background:linear-gradient(180deg,#e6e6e3,#d9dad6)}
.map-badge{position:absolute;left:445px;top:58px;width:160px;height:84px;background:var(--white);display:flex;flex-direction:column;align-items:center;justify-content:center;box-shadow:0 2px 6px rgba(0,0,0,.2)}
.map-badge .brand-name{font-size:22px}
.map-badge .brand-sub{font-size:8px;letter-spacing:2px}
.map-pin{position:absolute;left:628px;top:72px}

/* footer */
.site-footer{height:48px;background:var(--footer);color:var(--white);display:flex;align-items:center;padding:0 40px;font-size:11px}
.socials{margin-left:auto;display:flex;gap:8px}
.socials span{width:18px;height:18px;border-radius:50%;background:rgba(255,255,255,.85)}
</style>
</head>
<body>

<header class="site-header">
  <div class="brand"><span class="brand-name">CORVANE</span><span class="brand-sub">LENDING PARTNERS</span></div>
  <div class="header-contacts">
    <div class="hc-item">
      <span class="hc-icon"><svg width="14" height="14" viewBox="0 0 24 24"><path d="M6.6 10.8a15 15 0 0 0 6.6 6.6l2.2-2.2a1 1 0 0 1 1-.25 11.4 11.4 0 0 0 3.6.57 1 1 0 0 1 1 1V20a1 1 0 0 1-1 1A17 17 0 0 1 3 4a1 1 0 0 1 1-1h3.5a1 1 0 0 1 1 1c0 1.25.2 2.45.57 3.57a1 1 0 0 1-.25 1z" fill="#2b6cb0"/></svg></span>
      <div><b>Call Us</b>123 456 7890</div>
    </div>
    <div class="hc-item">
      <span class="hc-icon"><svg width="14" height="14" viewBox="0 0 24 24"><rect x="3" y="5" width="18" height="14" rx="1" fill="none" stroke="#2b6cb0" stroke-width="2"/><path d="M3 6l9 7 9-7" fill="none" stroke="#2b6cb0" stroke-width="2"/></svg></span>
      <div><b>Email Us</b>inquiry@corvanelending.com</div>
    </div>
  </div>
  <span class="btn-quote">GET A QUOTE</span>
</header>

<section class="hero">
  <div class="hero-photo" role="img" aria-label="Upward view of glass office towers against a blue sky"></div>
  <nav class="main-nav">
    <a class="active">HOME</a><a>ABOUT US</a><a>LOAN PROGRAMS</a><a>LOAN CRITERIA</a><a>NEWS</a><a>APPLY NOW</a><a>CONTACT US</a>
  </nav>
  <div class="hero-copy">
    <h1>WE ARE FULL SERVICE FINANCE COMPANY<br>SPECIALIZING IN OBTAINING CAPITAL<br>FOR SMALL BUSINESS.</h1>
    <span class="btn">CONTACT US TODAY</span>
  </div>
</section>

<section class="about">
  <h2 class="section-title">ABOUT <span>CORVANE</span></h2>
  <div class="title-rule"></div>
  <p class="lead">Nullam euismod, augue at fermentum sodales, augue nisi sagittis metus, eu sagittis ex nisl sed magna.</p>
  <p class="body">We help small business owners access the capital they need to launch, grow or sustain their business. Many of our programs offer flexible guidelines to overcome common obstacles such as credit score, credit history, time in business, financials and industry type. Our streamlined funding process makes getting a business loan, a line of credit or a commercial real estate loan a smooth and stress free experience for every client we serve, from first call to final funding.</p>
  <span class="btn">READ MORE</span>
</section>

<section class="closed">
  <h2 class="section-title">RECENTLY <span>CLOSED LOANS</span></h2>
  <div class="title-rule"></div>
  <span class="slider-arrow" style="left:160px"><svg width="10" height="10" viewBox="0 0 10 10"><path d="M7 1L3 5l4 4" stroke="#fff" stroke-width="2" fill="none"/></svg></span>
  <span class="slider-arrow" style="right:160px"><svg width="10" height="10" viewBox="0 0 10 10"><path d="M3 1l4 4-4 4" stroke="#fff" stroke-width="2" fill="none"/></svg></span>
  <div class="loan-cards">
    <div class="loan-card"><div class="kind">OFFICE BUILDING</div><div class="amount">$ 2,750,000</div><div class="note">Discounted Payoff<br>Wall Township</div></div>
    <div class="loan-card featured"><div class="kind">MIXED USE</div><div class="amount">$ 1,125,000</div><div class="note">Refinance Rate/Cash<br>New York</div></div>
    <div class="loan-card"><div class="kind">MIXED USE COMMERCIAL</div><div class="amount">$ 12,550,000</div><div class="note">Rehab Property Improvement<br>Paterson, NJ</div></div>
  </div>
</section>

<section class="news">
  <h2 class="section-title">LATEST <span>NEWS</span></h2>
  <div class="title-rule"></div>
  <div class="news-row one">
    <div class="news-panel" style="width:810px">
      <h3>PROIN EUISMOD, EST MOLLIS TEMPOR CONVALLIS, MASSA IPSUM SEMPER EX, AT MATTIS SEM VELIT MATTIS ARCU.</h3>
      <p>Quisque vitae lorem at nisi tincidunt faucibus. Curabitur ut ante non odio pretium tempor. Donec vel nunc a elit aliquet sagittis, sed feugiat magna sodales vitae. Morbi posuere massa non lectus porta, in blandit erat dapibus.</p>
      <span class="more">Read More...</span>
    </div>
    <div class="photo" style="flex:1;background:linear-gradient(160deg,#9fc0df,#3a6a9c 60%,#1f3f66)" role="img" aria-label="Glass skyscrapers seen from street level"></div>
  </div>
  <div class="news-row two">
    <div class="photo" style="width:420px;background:linear-gradient(180deg,#2d4f7a 0%,#5d84ad 45%,#c79a5a 80%,#3a3f48 100%)" role="img" aria-label="Modern office building at dusk with lit windows"></div>
    <div class="news-panel" style="flex:1;padding-top:40px">
      <h3>PROIN EUISMOD, EST MOLLIS TEMPOR CONVALLIS, MASSA IPSUM SEMPER EX, AT MATTIS SEM VELIT MATTIS ARCU.</h3>
      <p>Quisque vitae lorem at nisi tincidunt faucibus. Curabitur ut ante non odio pretium tempor. Donec vel nunc a elit aliquet sagittis, sed feugiat magna sodales vitae. Morbi posuere massa non lectus porta, in blandit erat dapibus.</p>
      <span class="more">Read More...</span>
    </div>
  </div>
</section>

<section class="programs">
  <h2 class="section-title">LOAN <span>PROGRAMS</span></h2>
  <div class="title-rule"></div>
  <div class="program-grid">
    <div class="program"><span class="program-icon"><svg width="26" height="26" viewBox="0 0 24 24"><circle cx="12" cy="12" r="8" fill="none" stroke="#fff" stroke-width="2"/><path d="M12 7v10M9 10h6M9 14h6" stroke="#fff" stroke-width="2"/></svg></span><div><h4>WORKING CAPITAL</h4><p>Sed a pulvinar sapien. Aenean eleifend eget quis malesuada.</p></div></div>
    <div class="program"><span class="program-icon"><svg width="26" height="26" viewBox="0 0 24 24"><rect x="4" y="6" width="16" height="12" rx="1" fill="none" stroke="#fff" stroke-width="2"/><path d="M4 10h16" stroke="#fff" stroke-width="2"/></svg></span><div><h4>DEBT CONSOLIDATIONS</h4><p>Sed a pulvinar sapien. Aenean eleifend eget quis malesuada.</p></div></div>
    <div class="program"><span class="program-icon"><svg width="26" height="26" viewBox="0 0 24 24"><path d="M3 14l5-3 4 2 6-4 3 2v6H3z" fill="#fff"/></svg></span><div><h4>PAYROLL</h4><p>Sed a pulvinar sapien. Aenean eleifend eget quis malesuada.</p></div></div>
    <div class="program"><span class="program-icon"><svg width="26" height="26" viewBox="0 0 24 24"><circle cx="12" cy="12" r="4" fill="none" stroke="#fff" stroke-width="2"/><circle cx="12" cy="12" r="8" fill="none" stroke="#fff" stroke-width="2" stroke-dasharray="3 2"/></svg></span><div><h4>OPERATING EXPENSES</h4><p>Sed a pulvinar sapien. Aenean eleifend eget quis malesuada.</p></div></div>
    <div class="program"><span class="program-icon"><svg width="26" height="26" viewBox="0 0 24 24"><rect x="5" y="5" width="14" height="14" fill="none" stroke="#fff" stroke-width="2"/><path d="M5 12h14M12 5v14" stroke="#fff" stroke-width="2"/></svg></span><div><h4>INVENTORY</h4><p>Sed a pulvinar sapien. Aenean eleifend eget quis malesuada.</p></div></div>
    <div class="program"><span class="program-icon"><svg width="26" height="26" viewBox="0 0 24 24"><circle cx="12" cy="12" r="7" fill="none" stroke="#fff" stroke-width="2"/><circle cx="12" cy="12" r="2" fill="#fff"/></svg></span><div><h4>EQUIPMENT FINANCING</h4><p>Sed a pulvinar sapien. Aenean eleifend eget quis malesuada.</p></div></div>
    <div class="program"><span class="program-icon"><svg width="26" height="26" viewBox="0 0 24 24"><path d="M4 20V9l8-5 8 5v11z" fill="none" stroke="#fff" stroke-width="2"/><rect x="10" y="13" width="4" height="7" fill="#fff"/></svg></span><div><h4>COMMERCIAL REAL ESTATE</h4><p>Sed a pulvinar sapien. Aenean eleifend eget quis malesuada.</p></div></div>
    <div class="program"><span class="program-icon"><svg width="26" height="26" viewBox="0 0 24 24"><path d="M3 12h6l3 3 3-3h6" fill="none" stroke="#fff" stroke-width="2"/><path d="M6 9l3 3M18 9l-3 3" stroke="#fff" stroke-width="2"/></svg></span><div><h4>BUSINESS ACQUISITIONS</h4><p>Sed a pulvinar sapien. Aenean eleifend eget quis malesuada.</p></div></div>
    <div class="program"><span class="program-icon"><svg width="26" height="26" viewBox="0 0 24 24"><path d="M12 3v18M3 12h18M6 6l12 12M18 6L6 18" stroke="#fff" stroke-width="2"/></svg></span><div><h4>BUSINESS EXPANSION</h4><p>Sed a pulvinar sapien. Aenean eleifend eget quis malesuada.</p></div></div>
  </div>
</section>

<section class="team">
  <h2 class="section-title">OUR <span>TEAM</span></h2>
  <div class="title-rule"></div>
  <span class="slider-arrow" style="left:140px"><svg width="10" height="10" viewBox="0 0 10 10"><path d="M7 1L3 5l4 4" stroke="#fff" stroke-width="2" fill="none"/></svg></span>
  <span class="slider-arrow" style="right:140px"><svg width="10" height="10" viewBox="0 0 10 10"><path d="M3 1l4 4-4 4" stroke="#fff" stroke-width="2" fill="none"/></svg></span>
  <div class="team-cards">
    <div class="team-card featured">
      <div class="team-photo" style="background:linear-gradient(180deg,#e9edf1,#b9c6d4)" role="img" aria-label="Headshot of a team member in a suit"></div>
      <div class="team-tag"><div class="name">MR. DANIEL HARLOW</div><div class="role">Marketing Manager</div><div class="line">123 456 7890</div><div class="line">daniel@corvanelending.com</div></div>
    </div>
    <div class="team-card">
      <div class="team-photo" style="background:linear-gradient(180deg,#eef0ef,#c7cfcc)" role="img" aria-label="Headshot of a team member in an office"></div>
      <div class="team-tag"><div class="name">MRS. CLARA WINSLOW</div><div class="role">Loan Officer</div></div>
    </div>
    <div class="team-card">
      <div class="team-photo" style="background:linear-gradient(180deg,#f1eee9,#cfc6ba)" role="img" aria-label="Headshot of a team member at a desk"></div>
      <div class="team-tag"><div class="name">MR. OWEN PRITCHARD</div><div class="role">Marketing Manager</div></div>
    </div>
  </div>
</section>

<section class="contact">
  <div class="contact-bg" role="img" aria-label="Dark backdrop of climbers helping each other up a cliff at sunset"></div>
  <div class="contact-inner">
    <h2>CONTACT US</h2>
    <div class="title-rule"></div>
    <div class="contact-body">
      <div class="contact-info">
        <div class="brand"><span class="brand-name">CORVANE</span><span class="brand-sub">LENDING PARTNERS</span></div>
        <ul>
          <li><svg width="12" height="12" viewBox="0 0 24 24"><path d="M12 2a7 7 0 0 0-7 7c0 5 7 13 7 13s7-8 7-13a7 7 0 0 0-7-7z" fill="#fff"/></svg><b>CORVANE LENDING PARTNERS</b></li>
          <li style="padding-left:22px">482 Halden Avenue, Suite 210, Columbus, Ohio 43215</li>
          <li><svg width="12" height="12" viewBox="0 0 24 24"><rect x="3" y="5" width="18" height="14" fill="none" stroke="#fff" stroke-width="2"/><path d="M3 6l9 7 9-7" fill="none" stroke="#fff" stroke-width="2"/></svg>inquiry@corvanelending.com</li>
          <li><svg width="12" height="12" viewBox="0 0 24 24"><path d="M6.6 10.8a15 15 0 0 0 6.6 6.6l2.2-2.2a1 1 0 0 1 1-.25 11.4 11.4 0 0 0 3.6.57 1 1 0 0 1 1 1V20a1 1 0 0 1-1 1A17 17 0 0 1 3 4a1 1 0 0 1 1-1h3.5a1 1 0 0 1 1 1c0 1.25.2 2.45.57 3.57a1 1 0 0 1-.25 1z" fill="#fff"/></svg>123 456 7890</li>
        </ul>
      </div>
      <div class="contact-form">
        <div class="field">Name</div>
        <div class="field">Email Address</div>
        <div class="field">Phone No.</div>
        <div class="field msg">Message</div>
        <span class="btn">SUBMIT</span>
      </div>
    </div>
  </div>
</section>

<section class="map">
  <div class="map-area" role="img" aria-label="Street map showing the office location"></div>
  <div class="map-badge"><span class="brand-name serif" style="font-weight:700;color:var(--blue-dark)">CORVANE</span><span class="brand-sub serif" style="font-weight:700;color:var(--blue-dark)">LENDING PARTNERS</span></div>
  <svg class="map-pin" width="30" height="40" viewBox="0 0 24 32"><path d="M12 0a10 10 0 0 0-10 10c0 8 10 22 10 22s10-14 10-22A10 10 0 0 0 12 0z" fill="#2b6cb0"/><circle cx="12" cy="10" r="4" fill="#fff"/></svg>
</section>

<footer class="site-footer">
  <span>Copyright © 2018 Corvane Lending Partners. All Rights Reserved.</span>
  <div class="socials"><span></span><span></span><span></span><span></span></div>
</footer>

</body>
</html>
```